Business card design for my company.
I would like the card's background colour to be black. You can also see our web site to get an idea of our brand. https://www.tmwhomecrafting.com.au/
- Name
- Email

```html
<!DOCTYPE html>
<html lang="en">
<head>
<meta charset="utf-8">
<title>TMW Home Crafting – Business Card</title>
<link href="https://fonts.googleapis.com/css2?family=Barlow+Condensed:wght@700&family=Montserrat:wght@400&display=swap" rel="stylesheet">
<style>
  :root {
    --page-bg: #d9d9d9;
    --card-black: #0b0b0b;
    --card-sheen: #1c1c1c;
    --brand-green: #1f9a45;
    --text-white: #ffffff;
    --badge-silver: #c4c4c4;
    --badge-gold: #c7a447;
    --badge-dark: #262626;
    --badge-ring: #9a9a9a;
    --badge-orange: #f4a21f;
    --badge-pale: #eef2f8;
    --badge-blue: #2a5db0;
  }
  * { box-sizing: border-box; margin: 0; padding: 0; }
  html, body { width: 1200px; height: 886px; overflow: hidden; }
  body {
    background: var(--page-bg);
    position: relative;
    font-family: "Montserrat", sans-serif;
  }
  .card {
    position: absolute;
    left: 290px;
    width: 620px;
    height: 378px;
    border-radius: 22px;
    overflow: hidden;
    background:
      linear-gradient(118deg, var(--card-black) 0%, var(--card-black) 38%, var(--card-sheen) 38.2%, var(--card-black) 70%);
    color: var(--text-white);
  }
  .card--front { top: 40px; }
  .card--back { top: 468px; }

  .wordmark {
    display: flex;
    align-items: center;
    gap: 12px;
    font-family: "Barlow Condensed", sans-serif;
    font-weight: 700;
    color: var(--text-white);
    letter-spacing: 2px;
    text-transform: uppercase;
    line-height: 1;
  }
  .wordmark__square {
    width: 22px;
    height: 22px;
    background: var(--brand-green);
    flex: none;
  }

  /* Front */
  .card--front .wordmark {
    position: absolute;
    top: 112px;
    left: 0; right: 0;
    justify-content: center;
    font-size: 46px;
  }
  .front__rule {
    position: absolute;
    top: 205px;
    left: 270px;
    width: 80px;
    height: 3px;
    background: var(--brand-green);
  }
  .front__website {
    position: absolute;
    top: 296px;
    left: 0; right: 0;
    text-align: center;
    font-size: 19px;
    letter-spacing: 0.3px;
  }

  /* Back */
  .card--back .wordmark {
    position: absolute;
    top: 168px;
    left: 42px;
    font-size: 36px;
  }
  .back__name {
    position: absolute;
    top: 258px;
    left: 62px;
    font-family: "Barlow Condensed", sans-serif;
    font-weight: 700;
    font-size: 34px;
    letter-spacing: 0.5px;
    text-transform: uppercase;
  }
  .back__email {
    position: absolute;
    top: 302px;
    left: 62px;
    font-size: 17px;
  }
  .back__tab {
    position: absolute;
    top: 262px;
    left: 0;
    width: 30px;
    height: 62px;
    background: var(--brand-green);
  }
  .awards {
    position: absolute;
    top: 0;
    left: 0;
    width: 620px;
    height: 378px;
  }
</style>
</head>
<body>
  <section class="card card--front" aria-label="Business card front">
    <div class="wordmark"><span class="wordmark__square"></span>TMW Home Crafting</div>
    <div class="front__rule"></div>
    <p class="front__website">www.tmwhomecrafting.com.au</p>
  </section>

  <section class="card card--back" aria-label="Business card back">
    <svg class="awards" viewBox="0 0 620 378" role="img" aria-label="Industry award badges">
      <circle cx="400" cy="110" r="27" fill="var(--badge-silver)"/>
      <circle cx="425" cy="178" r="27" fill="var(--badge-silver)"/>
      <circle cx="450" cy="246" r="27" fill="var(--badge-pale)" stroke="var(--badge-blue)" stroke-width="4"/>
      <circle cx="465" cy="72" r="27" fill="var(--badge-gold)"/>
      <circle cx="490" cy="140" r="27" fill="var(--badge-gold)"/>
      <circle cx="515" cy="208" r="27" fill="var(--badge-dark)" stroke="var(--badge-ring)" stroke-width="3"/>
      <circle cx="530" cy="34" r="27" fill="var(--badge-dark)" stroke="var(--badge-ring)" stroke-width="3"/>
      <circle cx="555" cy="102" r="27" fill="var(--badge-dark)" stroke="var(--badge-ring)" stroke-width="3"/>
      <circle cx="580" cy="170" r="27" fill="var(--badge-orange)"/>
    </svg>
    <div class="wordmark"><span class="wordmark__square"></span>TMW Home Crafting</div>
    <div class="back__tab"></div>
    <p class="back__name">Your Name Here</p>
    <p class="back__email">youremail@tmwhomecrafting.com.au</p>
  </section>
</body>
</html>
```